Veltrano.co - Polar Expeditions Specialists

We need a modern, visually striking business card for Veltrano.co, a company specialized in selling expedition cruises to the most remote regions on Earth, with a focus on the Arctic and Antarctica. The design should instantly communicate that the cardholder is an expert in polar travel. Use clean, premium aesthetics with cool tones like icy blue and white, possibly incorporating polar imagery (ice, glaciers, penguins, etc.)

Attached the logo

Contact Information for Business Card

Feels high-end and trustworthy.. Visually memorable — encourages people to keep it

Colors
0054AA
0677BA
7BADD7
CADEEF
E8F1F8

Requirements
Must have
• ice, glaciers, penguins, montains
Nice to have
• modern, transparente,

```html
<!DOCTYPE html>
<html lang="en">
<head>
<meta charset="UTF-8">
<title>Veltrano.co Business Card</title>
<link href="https://fonts.googleapis.com/css2?family=Poppins:wght@400;500;600;700&display=swap" rel="stylesheet">
<style>
  :root {
    --backdrop: #232427;
    --brand-blue: #2f6fae;
    --deep-blue: #0054aa;
    --ink: #1c1c1c;
    --paper: #ffffff;
    --steel: #8a8c90;
  }
  * { margin: 0; padding: 0; box-sizing: border-box; }
  html, body {
    width: 1200px; height: 900px; overflow: hidden;
    background: var(--backdrop);
    font-family: "Poppins", sans-serif;
  }
  .stage { position: relative; width: 1200px; height: 900px; }
  .card {
    position: absolute; width: 620px; height: 354px;
    border-radius: 26px; overflow: hidden;
  }
  /* Front */
  .card-front {
    left: 290px; top: 60px; background: var(--brand-blue);
    display: flex; flex-direction: column; align-items: center; justify-content: center;
    color: var(--paper);
  }
  .front-mark {
    width: 70px; height: 70px; border-radius: 50%;
    background: var(--paper); margin-bottom: 16px;
  }
  .front-name { font-size: 66px; font-weight: 700; line-height: 1; letter-spacing: 0.5px; }
  .front-tagline { font-size: 19px; font-weight: 600; margin-top: 8px; letter-spacing: 0.3px; }
  /* Back */
  .card-back { left: 290px; top: 486px; background: var(--paper); color: var(--ink); }
  .brand-lockup { position: absolute; left: 40px; top: 34px; display: flex; align-items: center; gap: 18px; }
  .brand-mark { width: 62px; height: 62px; border-radius: 50%; background: var(--brand-blue); }
  .brand-name { font-size: 46px; font-weight: 700; color: var(--brand-blue); line-height: 1; }
  .brand-tagline { font-size: 14px; font-weight: 600; color: var(--brand-blue); margin-top: 4px; }
  .holder { position: absolute; left: 40px; top: 150px; }
  .holder-name { font-size: 26px; font-weight: 700; color: var(--brand-blue); line-height: 1.1; }
  .holder-role { font-size: 15px; font-weight: 400; }
  .divider { position: absolute; left: 40px; top: 216px; width: 540px; height: 2px; background: var(--deep-blue); }
  .contacts { position: absolute; left: 40px; top: 228px; list-style: none; font-size: 15px; line-height: 25px; }
  .contacts li { display: flex; align-items: center; gap: 10px; }
  .contacts svg { width: 13px; height: 13px; fill: var(--deep-blue); }
  .address { position: absolute; right: 40px; top: 262px; font-size: 15px; line-height: 22px; text-align: left; }
  .edge-band { position: absolute; left: 0; bottom: 0; width: 620px; height: 30px; }
</style>
</head>
<body>
<main class="stage">
  <section class="card card-front">
    <div class="front-mark"></div>
    <div class="front-name">Veltrano.co</div>
    <div class="front-tagline">Polar Expeditions Specialists</div>
  </section>

  <section class="card card-back">
    <div class="brand-lockup">
      <div class="brand-mark"></div>
      <div>
        <div class="brand-name">Veltrano.co</div>
        <div class="brand-tagline">Polar Expeditions Specialists</div>
      </div>
    </div>
    <div class="holder">
      <div class="holder-name">Marlon Keswick</div>
      <div class="holder-role">CEO &amp; Founder</div>
    </div>
    <div class="divider"></div>
    <ul class="contacts">
      <li><svg viewBox="0 0 16 16"><path d="M3 1l3 3-2 2c1 2 3 4 5 5l2-2 3 3-2 3C6 14 2 10 1 3z"/></svg>+1.555.014.772</li>
      <li><svg viewBox="0 0 16 16"><path d="M1 3h14v10H1zM2 4l6 5 6-5z"/></svg>hello@veltrano.co</li>
      <li><svg viewBox="0 0 16 16"><circle cx="8" cy="8" r="7"/></svg>www.veltrano-polar.com</li>
    </ul>
    <div class="address">48 Harbor Lane,<br>Fairhaven, ME 04101 USA</div>
    <svg class="edge-band" viewBox="0 0 620 30" preserveAspectRatio="none" aria-hidden="true">
      <polygon points="0,16 392,16 378,30 0,30" fill="var(--brand-blue)"/>
      <polygon points="392,16 620,16 620,30 378,30" fill="var(--steel)"/>
    </svg>
  </section>
</main>
</body>
</html>
```